Velmora Systems Website

Website design for our company: Velmora Systems.
The website should look fresh and IT focused. Please have a look at http://www.velmorasystems.example.au/ for our current design. We want something fresh and new, professional looking, in WordPress so we can easily make changes.

It Company

```html
<!DOCTYPE html>
<html lang="en">
<head>
<meta charset="utf-8">
<title>Velmora Systems</title>
<link rel="stylesheet" href="https://fonts.googleapis.com/css2?family=Open+Sans:wght@300;400;600;700&display=swap">
<style>
:root{
  --green:#00a651;
  --green-dark:#007f3d;
  --green-mid:#00b95c;
  --green-light:#00d068;
  --blue:#1a73c4;
  --navy:#0b3f73;
  --navy-top:#1a63a8;
  --page:#efefef;
  --text:#444;
  --muted:#666;
  --white:#fff;
}
*{margin:0;padding:0;box-sizing:border-box}
html,body{width:1200px;height:930px;overflow:hidden}
body{background:var(--page);font-family:"Open Sans",Arial,sans-serif;color:var(--text);position:relative}
.abs{position:absolute}
.top-band{left:0;top:0;width:1200px;height:7px;background:var(--green)}

.brand{display:flex;align-items:center;gap:8px;border:3px solid var(--green);border-radius:4px;background:var(--white);padding:0 10px}
.brand-dot{width:16px;height:16px;border-radius:50%;background:var(--green);flex:none}
.brand-name{color:var(--green);font-weight:700;font-size:15px;line-height:1.1}
.brand--header{left:200px;top:15px;width:125px;height:63px}
.brand--welcome{left:875px;top:740px;width:125px;height:63px}

.ip-line{left:383px;top:19px;font-size:15.5px;font-weight:300;color:var(--muted);white-space:nowrap}

.main-nav{left:434px;top:52px;width:567px;height:25px;display:flex;background:linear-gradient(var(--navy-top),var(--navy));list-style:none;overflow:hidden}
.main-nav li{flex:1 1 auto;font-size:12.5px;color:var(--white);line-height:25px;text-align:center;white-space:nowrap}
.main-nav li.active{flex:0 0 63px;background:linear-gradient(#14b35e,#0a8d45)}

.slider{left:232px;top:102px;width:482px;height:308px;border:3px solid var(--white);box-shadow:0 0 3px rgba(0,0,0,.2)}
.slider-photo{width:100%;height:100%;background:linear-gradient(160deg,#c9c3b6 0%,#8f8a7d 30%,#b9b5ad 55%,#dedcd7 80%,#a9a6a0 100%)}
.slider-caption{left:236px;top:168px;width:191px;height:161px;background:rgba(40,40,40,.72);text-align:center;color:var(--white);padding-top:12px}
.slider-caption h2{font-weight:400;font-size:19px;line-height:24px}
.slider-caption p{font-size:11px;line-height:15px;margin-top:0;white-space:nowrap;letter-spacing:-.1px}
.slider-arrow{width:18px;height:38px}

.btn{display:flex;align-items:center;justify-content:center;color:var(--white);font-weight:700;font-size:10px;letter-spacing:.2px;border-radius:2px}
.btn--green{background:linear-gradient(#1a9a4f,#0a6b36);border:1px solid #0a5a2d}
.btn--blue{background:linear-gradient(#2a70b4,#0b3f73);border:1px solid #0a3560}

.remote{left:779px;top:101px;width:222px;height:91px;background:#f7f7f7;border:1px solid #ddd;padding:6px 8px}
.remote h3{font-weight:400;font-size:20.5px;color:var(--blue);line-height:24px}
.remote p{font-size:9.5px;color:#333;margin-top:2px}
.field{background:var(--white);border:1px solid #ccc;font-size:9px;color:#aaa;padding:0 6px;display:flex;align-items:center}

.testimonies-title{left:788px;top:204px;font-size:19.5px;color:var(--green);font-weight:400}
.testimonies{left:779px;top:231px;width:222px;list-style:none}
.testimonies li{display:flex;height:49px}
.testimonies li+li{border-top:1px solid #008a44}
.testimonies .date{width:33px;background:var(--green-dark);color:var(--white);font-size:8px;font-weight:600;display:flex;align-items:center;justify-content:center}
.testimonies .body{flex:1;background:var(--green-mid);padding:3px 6px;font-size:9.5px;line-height:12px;color:var(--white)}
.testimonies li:nth-child(2) .body{background:var(--green-light)}
.testimonies .name{color:#0a6a35;font-size:10.5px;line-height:13px}
.testimonies .more{color:#0a6a35;text-decoration:underline;margin-left:4px}

.shelf{left:0;top:522px;width:1200px;height:32px;background:linear-gradient(#f9f9f9,#dcdcdc 60%,#ececec)}
.feature-art{border-radius:4px}
.partner{border-radius:3px}

.feature{top:553px;width:207px;height:150px;text-align:center;padding:12px 14px 0}
.feature+.feature{border-left:1px solid #ddd}
.feature h4{font-weight:400;font-size:12px;line-height:14px;color:var(--blue);text-transform:uppercase}
.feature p{font-size:9.4px;line-height:13.5px;color:var(--muted);margin-top:2px}

.welcome{left:200px;top:715px;width:650px}
.welcome h1{font-weight:400;font-size:21.5px;color:var(--green);line-height:26px}
.welcome p{font-size:9.4px;line-height:14.5px;color:#333;letter-spacing:-.05px}

.footer{left:0;top:835px;width:1200px;height:95px;background:var(--green);border-top:2px solid #0a8a44}
.footer-links{left:201px;top:853px;width:220px;font-size:11.5px;line-height:18px;color:var(--white)}
.footer-links span{margin:0 4px}
.rights{left:201px;top:892px;font-size:9px;color:#1b58b0}
.contact-title{left:498px;top:846px;font-size:13px;color:var(--white);font-weight:400}
.footer-list{left:808px;top:847px;list-style:none;font-size:10px;line-height:16px;color:var(--white);font-weight:600}
.footer-list li::before{content:"•";margin-right:6px}
</style>
</head>
<body>
<div class="abs top-band"></div>

<div class="abs brand brand--header"><span class="brand-dot"></span><span class="brand-name">Velmora Systems</span></div>
<p class="abs ip-line">Your IP address is 203.0.113.45 which resolves to host-203-0-113-45.netlink.example.bo</p>

<ul class="abs main-nav">
  <li class="active">Home</li><li>Clients</li><li>Services</li><li>Supports</li><li>Testimonials</li><li>Contact Us</li><li>About Us</li>
</ul>

<div class="abs slider"><div class="slider-photo" role="img" aria-label="Photo of hands typing on a laptop keyboard in an office"></div></div>
<div class="abs slider-caption">
  <h2>Aliquam elit arcu,<br>iaculis se</h2>
  <p>mollis a, hendrerit a odio. Nam<br>placerat mi id semper gravida. Nunc<br>vel molestie ipsum, quis tincidunt</p>
</div>
<div class="abs btn btn--green" style="left:283px;top:283px;width:97px;height:32px">VIEW MORE</div>
<svg class="abs slider-arrow" style="left:201px;top:225px" viewBox="0 0 18 38"><polygon points="18,0 0,19 18,38" fill="#00a651"/></svg>
<svg class="abs slider-arrow" style="left:729px;top:225px" viewBox="0 0 18 38"><polygon points="0,0 18,19 0,38" fill="#00a651"/></svg>

<section class="abs remote">
  <h3>REMOTE SUPPORT</h3>
  <p>Enter your 6-digit code</p>
</section>
<div class="abs field" style="left:787px;top:156px;width:100px;height:22px">Code</div>
<div class="abs btn btn--blue" style="left:902px;top:156px;width:90px;height:21px">CONNECT NOW</div>

<h3 class="abs testimonies-title">LAST TESTIMONIES</h3>
<ul class="abs testimonies">
  <li><div class="date">JAN-28</div><div class="body"><div class="name">JOHN DOE</div>Adipiscing elit. Etiam sed sodales neque vitae orci pharetra rhoncus.<span class="more">Read more</span></div></li>
  <li><div class="date">JAN-28</div><div class="body"><div class="name">JOHN DOE</div>Adipiscing elit. Etiam sed sodales neque vitae orci pharetra rhoncus.<span class="more">Read more</span></div></li>
  <li><div class="date">JAN-28</div><div class="body"><div class="name">JOHN DOE</div>Adipiscing elit. Etiam sed sodales neque vitae orci pharetra rhoncus.<span class="more">Read more</span></div></li>
</ul>
<div class="abs btn btn--green" style="left:845px;top:389px;width:90px;height:19px">VIEW MORE</div>

<div class="abs shelf"></div>
<div class="abs feature-art" style="left:203px;top:432px;width:172px;height:118px;background:linear-gradient(90deg,#2a2a2e,#55575c 50%,#222326)" role="img" aria-label="Illustration of server racks"></div>
<div class="abs feature-art" style="left:418px;top:418px;width:156px;height:128px;background:linear-gradient(#9aa0a6,#6f757b 55%,#1f5ea8 75%,#b9bcc0)" role="img" aria-label="Illustration of gears above a laptop"></div>
<div class="abs feature-art" style="left:640px;top:433px;width:120px;height:115px;border-radius:50%;background:radial-gradient(circle at 40% 40%,#f4f4f4,#d94a3a 45%,#2c68c2 70%,#4a9a3a)" role="img" aria-label="Illustration of a word globe about consulting"></div>
<div class="abs partner" style="left:832px;top:455px;width:54px;height:32px;background:#1565b8"></div>
<div class="abs partner" style="left:893px;top:465px;width:102px;height:22px;background:#8a8d90"></div>
<div class="abs partner" style="left:812px;top:500px;width:62px;height:40px;background:linear-gradient(90deg,#e84a2a,#3aa53a,#1e7fd0,#f4b400)"></div>
<div class="abs partner" style="left:883px;top:504px;width:44px;height:28px;background:#1a5db2"></div>
<div class="abs partner" style="left:936px;top:496px;width:60px;height:36px;background:#d3242b"></div>

<div class="abs feature" style="left:185px">
  <h4>Lorem ipsum dolor sit amet, consectetur adipiscing elit.</h4>
  <p>Morbi risus risus, imperdiet at ligula a, vulputate ultricies justo. Curabitur porta dolor ac congue venenatis. Vivamus adipiscing lorem augue, at viverra ligula</p>
</div>
<div class="abs feature" style="left:392px">
  <h4>Lorem ipsum dolor sit amet, consectetur adipiscing elit.</h4>
  <p>Morbi risus risus, imperdiet at ligula a, vulputate ultricies justo. Curabitur porta dolor ac congue venenatis. Vivamus adipiscing lorem augue, at viverra ligula</p>
</div>
<div class="abs feature" style="left:599px">
  <h4>Lorem ipsum dolor sit amet, consectetur adipiscing elit.</h4>
  <p>Morbi risus risus, imperdiet at ligula a, vulputate ultricies justo. Curabitur porta dolor ac congue venenatis. Vivamus adipiscing lorem augue, at viverra ligula</p>
</div>
<div class="abs feature" style="left:806px">
  <h4>Our partners.</h4>
  <p>Morbi risus risus, imperdiet at ligula a, vulputate ultricies justo. Curabitur porta dolor ac congue venenatis. Vivamus adipiscing lorem augue, at viverra ligula gravida sed.</p>
</div>
<div class="abs btn btn--blue" style="left:240px;top:661px;width:98px;height:32px">VIEW MORE</div>
<div class="abs btn btn--blue" style="left:448px;top:661px;width:98px;height:32px">VIEW MORE</div>
<div class="abs btn btn--blue" style="left:655px;top:661px;width:98px;height:32px">VIEW MORE</div>
<div class="abs btn btn--blue" style="left:862px;top:661px;width:98px;height:32px">VIEW MORE</div>

<section class="abs welcome">
  <h1>Welcome to Velmora Systems</h1>
  <p>Velmora Systems is an Adelaide based company with a single objective - to excel in the support and service of all computer and IT needs.<br>
  We provide a high level of consulting services using the most experienced engineers at a reasonable and fair price. We believe in using a Business Value approach to every aspect of computer consulting to provide our clients with the most cost effective solutions.<br>
  We strongly believe that we are in business with our clients. Each thing we do must be measured against our clients' business objectives. At the end of the day our client's success is our success.</p>
</section>
<div class="abs brand brand--welcome"><span class="brand-dot"></span><span class="brand-name">Velmora Systems</span></div>

<footer class="abs footer"></footer>
<div class="abs footer-links">Home<span>|</span>Clients<span>|</span>Services<span>|</span>Supports<br>Testimonials<span>|</span>Contact Us<span>|</span>About Us</div>
<p class="abs rights">All rights reserved</p>
<h5 class="abs contact-title">CONTACT</h5>
<div class="abs field" style="left:496px;top:867px;width:98px;height:19px">Name</div>
<div class="abs field" style="left:606px;top:867px;width:98px;height:19px">Email</div>
<div class="abs field" style="left:496px;top:892px;width:98px;height:19px">Phone</div>
<div class="abs btn btn--blue" style="left:626px;top:892px;width:58px;height:18px">SEND</div>
<ul class="abs footer-list">
  <li>Lorem ipsum dolor sit amet</li>
  <li>Consectetur adipiscing elit.</li>
  <li>Etiam egestas mi in volutpat tincidunt.</li>
  <li>Etiam fringilla enim eu lorem mattis</li>
</ul>
</body>
</html>
```